Brindlewick Solutions Ltd

I'd like to create a company letterhead for the attached logo in word format.

I'd like to emphasis the icon in large translucent state from the left corner and ensure that the letterhead colouring matches the colour palette of the current logo with a contrast so it's clear to see. I've attached a copy of our sister company page on the app for reference.

```html
<!DOCTYPE html>
<html lang="en">
<head>
<meta charset="utf-8">
<title>Brindlewick Solutions Ltd – Letterhead</title>
<link href="https://fonts.googleapis.com/css2?family=Lato:wght@400;700&display=swap" rel="stylesheet">
<style>
  :root {
    --ink: #2b2b2b;
    --ink-soft: #3a3a3a;
    --paper: #ffffff;
    --mist: #ededed;
    --mist-light: #f6f6f6;
  }
  html, body {
    margin: 0;
    padding: 0;
    width: 1061px;
    height: 1200px;
    overflow: hidden;
    background: var(--paper);
  }
  .letterhead {
    position: relative;
    width: 1061px;
    height: 1200px;
    background: var(--paper);
    font-family: "Lato", sans-serif;
    color: var(--ink);
    overflow: hidden;
  }
  .backdrop-rays {
    position: absolute;
    left: 0;
    top: 420px;
    width: 1061px;
    height: 780px;
    background:
      linear-gradient(90deg, var(--mist) 0%, var(--mist-light) 45%, rgba(255,255,255,0) 85%);
    opacity: 0.9;
  }
  .backdrop-ring {
    position: absolute;
    left: -8px;
    top: 850px;
    width: 420px;
    height: 420px;
  }
  .brand {
    position: absolute;
    left: 100px;
    top: 72px;
    width: 240px;
    text-align: center;
    color: var(--ink);
    font-weight: 400;
  }
  .brand-dot {
    display: block;
    width: 74px;
    height: 74px;
    margin: 0 auto 12px;
    border-radius: 50%;
    background: var(--ink);
  }
  .brand-name {
    display: block;
    font-size: 40px;
    line-height: 1;
    letter-spacing: 0.5px;
  }
  .brand-sub {
    display: block;
    margin-top: 4px;
    font-size: 11px;
    letter-spacing: 7.4px;
    text-transform: uppercase;
  }
  .contact {
    position: absolute;
    left: 100px;
    top: 975px;
    font-size: 16px;
    line-height: 22px;
    color: var(--ink-soft);
  }
  .contact-company { font-weight: 700; color: var(--ink); margin: 0; }
  .contact-address { margin: 0 0 12px; font-style: normal; }
  .contact-list { list-style: none; margin: 0; padding: 0; }
  .contact-list li { display: flex; align-items: center; gap: 8px; }
  .contact-icon { width: 14px; height: 14px; fill: var(--ink); flex: none; }
  .contact-web { margin: 8px 0 0; font-weight: 700; color: var(--ink); }
</style>
</head>
<body>
  <main class="letterhead">
    <div class="backdrop-rays" role="img" aria-label="Soft grey radiating light rays decoration"></div>
    <svg class="backdrop-ring" viewBox="0 0 420 420" aria-hidden="true">
      <circle cx="210" cy="210" r="180" fill="none" stroke="var(--mist)" stroke-width="36"/>
    </svg>

    <header class="brand">
      <span class="brand-dot"></span>
      <span class="brand-name">Brindlewick</span>
      <span class="brand-sub">Solutions Ltd</span>
    </header>

    <footer class="contact">
      <p class="contact-company">Brindlewick Solutions Ltd</p>
      <address class="contact-address">4527 Halden Road<br>Millbrook, CT 06402</address>
      <ul class="contact-list">
        <li>
          <svg class="contact-icon" viewBox="0 0 24 24"><path d="M6.6 10.8a15.1 15.1 0 0 0 6.6 6.6l2.2-2.2a1 1 0 0 1 1-.25 11.4 11.4 0 0 0 3.6.57 1 1 0 0 1 1 1V20a1 1 0 0 1-1 1A17 17 0 0 1 3 4a1 1 0 0 1 1-1h3.5a1 1 0 0 1 1 1c0 1.25.2 2.45.57 3.57a1 1 0 0 1-.25 1z"/></svg>
          (555) 014-2238
        </li>
        <li>
          <svg class="contact-icon" viewBox="0 0 24 24"><path d="M6 2h12v6H6zM3 9h18a1 1 0 0 1 1 1v7h-4v5H6v-5H2v-7a1 1 0 0 1 1-1zm5 7v4h8v-4z"/></svg>
          (555) 014-2238
        </li>
        <li>
          <svg class="contact-icon" viewBox="0 0 24 24"><path d="M2 5h20v14H2zm2 2v.5l8 5 8-5V7l-8 5z"/></svg>
          info@brindlewicksolutions.com
        </li>
      </ul>
      <p class="contact-web">brindlewicksolutions.com</p>
    </footer>
  </main>
</body>
</html>
```